Beacon Advisory Website

I currently have a website www.beaconadvisoryinc.com. We are a IT Consulting Company. Our website will pretty much tell out our services. I am looking to enhance my website and make it look more professional. Looking for very classy and Contemporary look and design for my website.

It Company

```html
<!DOCTYPE html>
<html lang="en">
<head>
<meta charset="utf-8">
<title>Beacon Advisory</title>
<link rel="stylesheet" href="https://fonts.googleapis.com/css2?family=Lato:wght@300;400;700;900&family=Raleway:wght@300;400;500&display=swap">
<style>
  :root {
    --blue: #0a78c2;
    --blue-light: #14a0df;
    --link: #1e63a8;
    --ink: #111;
    --muted: #8a8a8a;
    --rule: #d6d6d6;
    --footer: #000;
    --social: #222;
    --hero-dark: #141c2a;
  }
  * { box-sizing: border-box; margin: 0; padding: 0; }
  html, body { width: 922px; height: 1200px; overflow: hidden; background: #fff; }
  body { position: relative; font-family: "Lato", sans-serif; color: var(--ink); }

  .hero {
    position: absolute; left: 0; top: 0; width: 922px; height: 520px;
    background: radial-gradient(ellipse at 55% 35%, #3d4656 0%, #232b3a 45%, var(--hero-dark) 100%);
  }
  .main-nav {
    position: absolute; left: 59px; top: 0; width: 803px; height: 44px;
    background: #fff; z-index: 2;
  }
  .main-nav a {
    position: absolute; top: 0; height: 44px; line-height: 44px;
    font-family: "Raleway", sans-serif; font-size: 11.5px; font-weight: 400;
    color: #555; text-decoration: none; transform: translateX(-50%); white-space: nowrap;
  }
  .main-nav a.active {
    width: 80px; text-align: center; color: #fff;
    background: linear-gradient(#0fa2e0, var(--blue));
  }
  .brand {
    position: absolute; left: 260px; top: 210px; display: flex; align-items: center; gap: 22px;
  }
  .brand-mark { width: 90px; height: 90px; background: var(--blue-light); }
  .brand-name {
    font-family: "Lato", sans-serif; font-weight: 700; color: #fff;
    font-size: 44px; line-height: 1.05; letter-spacing: 3px;
  }

  .portrait {
    position: absolute; left: 40px; top: 584px; width: 316px; height: 482px;
    background: linear-gradient(#e9e2dc 0%, #c8b3a6 22%, #1d1d22 40%, #1b1b20 100%);
    border-radius: 120px 120px 0 0;
  }
  .about { position: absolute; left: 426px; top: 578px; width: 420px; }
  .about h2 {
    font-family: "Raleway", sans-serif; font-weight: 400; font-size: 21px;
    letter-spacing: 4px;
  }
  .about p {
    margin-top: 24px; font-size: 12.4px; line-height: 24px; color: var(--muted); font-weight: 400;
  }
  .about .more {
    display: inline-block; margin-top: 18px; font-family: "Raleway", sans-serif;
    font-size: 14.5px; letter-spacing: 3px; color: var(--ink); text-decoration: underline;
    text-underline-offset: 3px;
  }
  .divider { position: absolute; left: 380px; top: 820px; width: 508px; border-top: 1px solid var(--rule); }

  .service {
    position: absolute; top: 858px; width: 150px; transform: translateX(-50%); text-align: center;
  }
  .service-icon { width: 38px; height: 38px; margin: 0 auto; border-radius: 50%; }
  .service h3 { margin-top: 24px; font-size: 12.3px; font-weight: 400; }
  .service p { margin-top: 10px; font-size: 10.4px; line-height: 16px; color: var(--muted); }
  .service a { display: block; margin-top: 10px; font-size: 11.5px; color: var(--link); text-decoration: none; }

  .site-footer {
    position: absolute; left: 0; top: 1066px; width: 922px; height: 134px; background: var(--footer);
  }
  .social { position: absolute; left: 412px; top: 36px; display: flex; gap: 1px; }
  .social span { width: 32px; height: 32px; background: var(--social); }
  .copyright {
    position: absolute; top: 81px; width: 100%; text-align: center;
    font-size: 10.6px; color: #333;
  }
  .copyright b { font-weight: 400; color: var(--blue-light); }
</style>
</head>
<body>
  <header class="hero" role="img" aria-label="Business meeting photo with colleagues shaking hands at a table">
    <nav class="main-nav">
      <a class="active" href="#" style="left:160px">Home</a>
      <a href="#" style="left:253px">About Us</a>
      <a href="#" style="left:349px">Services</a>
      <a href="#" style="left:446px">Solutions</a>
      <a href="#" style="left:554px">Resources</a>
      <a href="#" style="left:652px">Career</a>
      <a href="#" style="left:746px">Contact Us</a>
    </nav>
    <div class="brand">
      <div class="brand-mark"></div>
      <div class="brand-name">BEACON<br>ADVISORY</div>
    </div>
  </header>

  <div class="portrait" role="img" aria-label="Portrait photo of a smiling businesswoman in a dark suit"></div>

  <section class="about">
    <h2>KNOW ABOUT US</h2>
    <p>Today’s IT market is a dynamic, fast-paced industry, with ever-increasing demands. Meeting these demands for over 25 years, Beacon Advisory maintains a global presence, aggressively recruiting expertly qualified IT and Management Professionals from around the world and cultivating key partnerships.</p>
    <a class="more" href="#">READ MORE</a>
  </section>
  <div class="divider"></div>

  <div class="service" style="left:460px">
    <div class="service-icon" role="img" aria-label="Light bulb icon" style="background:#d9dcd0"></div>
    <h3>Consulting</h3>
    <p>Beacon Advisory has certified professional consultants</p>
    <a href="#">READ MORE</a>
  </div>
  <div class="service" style="left:625px">
    <div class="service-icon" role="img" aria-label="Person with circular arrows icon" style="background:#c9dde6"></div>
    <h3>Staff Augmentation</h3>
    <p>For years Beacon Advisory as been offering our customers</p>
    <a href="#">READ MORE</a>
  </div>
  <div class="service" style="left:791px">
    <div class="service-icon" role="img" aria-label="Globe with people icon" style="background:#cfe3d6"></div>
    <h3>Offshore</h3>
    <p>Our Offshore development model has a unique distinction</p>
    <a href="#">READ MORE</a>
  </div>

  <footer class="site-footer">
    <div class="social"><span></span><span></span><span></span></div>
    <p class="copyright">© <b>BEACON ADVISORY</b> - 2016. All Rights Reserved.</p>
  </footer>
</body>
</html>
```